Business Card Design For Marketing Agnecy LVP

Need business card design for marketing agency.

Doug Fenwick
President, CEO
1-555-302-4196
doug@boldpromoperksgroup.example
www.BoldPromoPerksGroup.example

Back Side:
Boost Sales Using Rewards, Incentives & Giveaways
Get A Free Sample Package

Target Market(s)

B2B

Industry/Entity Type

Marketing

Contact Information for Business Card

Doug Fenwick
President, CEO
1-555-302-4196

Back Side:
Get A Free Sample Package

Please note that my current url is OLD DESIGN. I am working on new design and want the business card to match color themes at least on new site. Here is the demo link for new site so you can see the colors I use, etc.

http://layoutcratehub.example/kq/doug/lvp_final/index.html

Requirements
Must have
• Please note that my current url is OLD DESIGN. I am working on new design and want the business card to match color themes at least on new site. Here is the demo link for new site so you can see the colors I use, etc.

Nice to have

Should not have

```html
<!DOCTYPE html>
<html lang="en">
<head>
<meta charset="utf-8">
<title>LVP Business Card</title>
<link rel="stylesheet" href="https://fonts.googleapis.com/css2?family=Exo+2:wght@600;700&family=Roboto:wght@400;700&family=Roboto+Condensed:wght@400&display=swap">
<style>
  :root {
    --bg: #c9c9c9;
    --brand-blue: #2b5b9b;
    --brand-blue-dark: #244f8a;
    --ink-dark: #3a3a3c;
    --ink-body: #3b3b3b;
    --paper: #f4f4f4;
    --paper-shade: #e2e2e2;
    --banner: #f2f2f2;
    --white: #ffffff;
  }
  * { box-sizing: border-box; margin: 0; padding: 0; }
  html, body { width: 1200px; height: 576px; overflow: hidden; }
  body { background: var(--bg); position: relative; font-family: "Roboto", sans-serif; }

  .card {
    position: absolute;
    top: 139px;
    width: 484px;
    height: 291px;
    border-radius: 10px;
    overflow: hidden;
  }

  .wordmark {
    position: absolute;
    font-family: "Roboto", sans-serif;
    font-weight: 700;
    line-height: 1;
    letter-spacing: -1px;
  }

  /* Back side */
  .card--back { left: 82px; background: var(--brand-blue); color: var(--white); }
  .card--back .wordmark {
    left: 0; right: 0; top: 40px;
    text-align: center;
    font-size: 104px;
    color: var(--white);
  }

  .offer-banner { position: absolute; left: 62px; top: 193px; width: 360px; height: 54px; }
  .offer-banner svg { position: absolute; inset: 0; }
  .offer-banner__text { position: absolute; inset: 0; text-align: center; padding-top: 7px; }
  .offer-banner__tagline { font-size: 13px; line-height: 16px; color: var(--ink-body); }
  .offer-banner__cta { font-size: 13px; line-height: 16px; font-weight: 700; color: var(--brand-blue); margin-top: 3px; }

  .card--back .web {
    position: absolute; left: 0; right: 0; top: 255px;
    text-align: center; font-size: 13px; line-height: 16px;
  }

  /* Front side */
  .card--front {
    left: 602px;
    background: linear-gradient(160deg, var(--white), var(--paper) 50%, var(--paper-shade));
  }
  .card--front .wordmark {
    left: 44px; top: 108px;
    font-size: 74px;
    color: var(--brand-blue);
  }

  .person { position: absolute; left: 232px; top: 82px; }
  .person__name { font-family: "Exo 2", sans-serif; font-weight: 600; font-size: 20px; line-height: 24px; color: var(--brand-blue); }
  .person__title { font-size: 11.5px; line-height: 14px; color: var(--ink-body); margin-top: 2px; }

  .contacts {
    position: absolute; left: 232px; top: 143px; list-style: none;
    font-family: "Roboto Condensed", sans-serif; font-size: 12.5px; color: var(--ink-body);
  }
  .contacts li { display: flex; align-items: center; height: 18.5px; }
  .contacts svg { width: 11px; height: 11px; margin-right: 10px; fill: var(--brand-blue-dark); flex: none; }

  .cta-band { position: absolute; left: 0; bottom: 0; width: 484px; height: 37px; }
  .cta-band svg { position: absolute; inset: 0; }
  .cta-band__text {
    position: absolute; right: 22px; top: 12px;
    font-family: "Exo 2", sans-serif; font-weight: 700; font-size: 13.5px; line-height: 16px;
    letter-spacing: 0.5px; color: var(--white);
  }
</style>
</head>
<body>

<section class="card card--back" aria-label="Card back">
  <p class="wordmark">LVP</p>
  <div class="offer-banner">
    <svg width="360" height="54" viewBox="0 0 360 54">
      <path d="M4 0 H356 Q360 0 359 4 L349 42 L180 51 L11 42 L1 4 Q0 0 4 0 Z" fill="#f2f2f2"/>
    </svg>
    <div class="offer-banner__text">
      <p class="offer-banner__tagline">Boost Sales Using Rewards, Incentives &amp; Giveaways</p>
      <p class="offer-banner__cta">GET A FREE SAMPLE PACKAGE</p>
    </div>
  </div>
  <p class="web">www.BoldPromoPerksGroup.example</p>
</section>

<section class="card card--front" aria-label="Card front">
  <p class="wordmark">LVP</p>

  <div class="person">
    <h1 class="person__name">Doug Fenwick</h1>
    <p class="person__title">President, CEO</p>
  </div>

  <ul class="contacts">
    <li><svg viewBox="0 0 12 12"><path d="M1 3 Q6 0 11 3 L10 5 L8 4.5 L8 3.5 Q6 3 4 3.5 L4 4.5 L2 5 Z M3 6 H9 L10 11 H2 Z"/></svg>1-555-302-4196</li>
    <li><svg viewBox="0 0 12 12"><path d="M0 2 H12 V10 H0 Z M1 3 L6 7 L11 3" stroke="#f4f4f4" stroke-width="1"/></svg>doug@boldpromoperksgroup.example</li>
    <li><svg viewBox="0 0 12 12"><circle cx="6" cy="6" r="5.5"/><path d="M0.5 6 H11.5 M6 0.5 V11.5 M6 0.5 Q2.5 6 6 11.5 M6 0.5 Q9.5 6 6 11.5" stroke="#f4f4f4" stroke-width="0.8" fill="none"/></svg>www.BoldPromoPerksGroup.example</li>
  </ul>

  <div class="cta-band">
    <svg width="484" height="37" viewBox="0 0 484 37">
      <rect x="0" y="27" width="210" height="10" fill="#3a3a3c"/>
      <path d="M196 37 L211 6 Q214 1 220 1 H484 V37 Z" fill="#2b5b9b"/>
    </svg>
    <span class="cta-band__text">GET A FREE SAMPLE PACKAGE</span>
  </div>
</section>

</body>
</html>
```